Banner to be displayed at local Farmers Market Booth.

Graphic Design Brief: Farmers Market Banner Contest

Project Overview:We are seeking talented graphic designers to create a visually appealing banner for our booth at the local farmers market. Our company specializes in healthy, all-natural dog and cat treats, and we want a banner that captures our brand identity while drawing in pet owners who value quality and nutrition for their furry friends.

Banner Specifications:

Size: 24 inches x 60 inches (Horizontal orientation) 24" High X 60 wide

Theme: Vintage/Retro

Style: Warm, inviting, nostalgic with a touch of rustic charm

Colors: Earthy, muted tones such as warm browns, soft greens, and creamy yellows. Pops of red or blue may be used sparingly for accents. OR Black and White with gray scales. Would like to see both

Typography: Retro-style fonts that are readable and align with the vintage aesthetic.

Key Elements to Include: website (www.moltbyfarms.com)

Company Name: Moltby Farms

Tagline: " Simply Honest Bites "
Imagery: Illustrations or stylized graphics of happy dogs and cats, possibly interacting with treats.

Emphasis on Natural Ingredients: Icons or design elements that subtly suggest freshness and quality (e.g., leaves, wheat, bones, or paw prints).

Farmers Market Appeal: A design that blends well with the artisanal, handmade, and farm-fresh atmosphere of the market.

Design Considerations:

The banner should be easily readable from a distance.

A balanced composition that doesn't feel overcrowded.

Should evoke trust and warmth while maintaining a professional look.

Avoid overly modern or sleek elements that don’t align with the vintage aesthetic.

Submission Requirements:

High-resolution digital file in PDF or AI format.

CMYK color mode for printing purposes.

Must include a mockup or preview of how it would look in a real farmers market setting.

We look forward to seeing your creative interpretations of our brand! If you have any questions, feel free to reach out.

Font styles to use
Other font styles liked:
• See attachement

Requirements
Nice to have
• Retro/Vintage,playful BUT NOT whimsical

```html
<!DOCTYPE html>
<html lang="en">
<head>
<meta charset="utf-8">
<title>Moltby Farms – Market Banner</title>
<link rel="stylesheet" href="https://fonts.googleapis.com/css2?family=Lexend+Zetta:wght@900&family=Libre+Baskerville:wght@400;700&display=swap">
<style>
  :root {
    --backdrop: #dcc9ba;
    --banner-white: #ffffff;
    --forest-ink: #15231f;
    --illus-light: #e9eae8;
    --illus-mid: #8f9694;
    --illus-dark: #3a4340;
  }
  html, body {
    margin: 0;
    padding: 0;
    width: 1200px;
    height: 581px;
    overflow: hidden;
    background: var(--backdrop);
  }
  .canvas {
    position: relative;
    width: 1200px;
    height: 581px;
    overflow: hidden;
  }
  .banner {
    position: absolute;
    left: 47px;
    top: 69px;
    width: 1106px;
    height: 442px;
    background: var(--banner-white);
  }
  .banner-art {
    position: absolute;
    left: 0;
    top: 0;
    width: 1200px;
    height: 581px;
  }
  .grunge-field { fill: var(--forest-ink); }
  .tagline {
    font-family: "Lexend Zetta", sans-serif;
    font-weight: 900;
    fill: var(--banner-white);
  }
  .web-address {
    font-family: "Libre Baskerville", serif;
    font-weight: 400;
    fill: var(--banner-white);
  }
  .company-name {
    font-family: "Libre Baskerville", serif;
    font-weight: 700;
    fill: var(--forest-ink);
  }
  .company-line {
    font-family: "Libre Baskerville", serif;
    font-weight: 700;
    fill: var(--forest-ink);
  }
  .pet-illustration {
    position: absolute;
    left: 720px;
    top: 116px;
    width: 407px;
    height: 289px;
    background: linear-gradient(135deg, var(--illus-light) 0%, var(--illus-mid) 55%, var(--illus-dark) 100%);
    clip-path: polygon(0 0, 69% 0, 69% 34%, 100% 34%, 100% 100%, 0 100%);
  }
  .brand-mark {
    position: absolute;
    left: 1006px;
    top: 136px;
    width: 116px;
    display: flex;
    align-items: center;
    gap: 5px;
    font-family: "Libre Baskerville", serif;
    font-weight: 400;
    font-size: 12px;
    line-height: 1;
    color: var(--banner-white);
    white-space: nowrap;
  }
  .brand-dot {
    flex: none;
    width: 9px;
    height: 9px;
    border-radius: 50%;
    background: var(--banner-white);
  }
</style>
</head>
<body>
<div class="canvas">
  <div class="banner"></div>

  <svg class="banner-art" viewBox="0 0 1200 581" xmlns="http://www.w3.org/2000/svg">
    <path class="grunge-field" d="
      M77 92 L95 86 L112 93 L130 87 L150 91 L172 85 L195 92 L220 86 L248 90 L275 84 L300 91
      L330 86 L360 92 L395 85 L430 90 L465 86 L500 92 L540 85 L580 90 L620 86 L660 91 L700 85
      L740 90 L780 86 L820 92 L860 86 L900 91 L940 85 L980 90 L1020 86 L1060 92 L1100 87 L1130 93
      L1127 130 L1133 170 L1126 210 L1132 250 L1127 290 L1133 330 L1128 370 L1132 392
      L1110 396 L1085 402 L1060 398 L1030 404 L1000 399 L970 405 L940 400 L905 404 L870 399
      L835 403 L800 400 L765 404 L735 398 L715 392
      L700 378 L685 368 L668 372 L650 362 L632 370 L612 360 L592 366 L570 358 L548 366
      L525 362 L500 370 L478 364 L455 372 L430 366 L405 372 L380 364 L355 370 L330 360
      L308 356 L290 366 L270 374 L245 380 L220 376 L195 384 L170 380 L145 388 L118 384 L95 390 L78 386
      L72 350 L78 310 L71 270 L77 230 L70 190 L76 150 L71 120 Z"/>

    <text class="tagline" x="84" y="212" font-size="56" textLength="613" lengthAdjust="spacingAndGlyphs">SIMPLY HONEST</text>
    <text class="tagline" x="349" y="278" font-size="62" textLength="348" lengthAdjust="spacingAndGlyphs">BITES</text>

    <text class="web-address" x="132" y="328" font-size="26" textLength="534" lengthAdjust="spacing">WWW.MOLTBYFARMS.COM</text>

    <text class="company-name" x="82" y="437" font-size="52" textLength="594" lengthAdjust="spacing">MOLTBY FARMS</text>
    <text class="company-line" x="82" y="487" font-size="37" textLength="1006" lengthAdjust="spacingAndGlyphs">PURVEYORS OF PREMIUM PET FOOD &amp; TREATS</text>
  </svg>

  <div class="pet-illustration" role="img" aria-label="Black and white illustration of a fluffy dog lying beside a tabby cat"></div>

  <div class="brand-mark"><span class="brand-dot"></span>Moltby Farms</div>
</div>
</body>
</html>
```